Dunmore Roofing

Want a professional looking business card

Industry/Entity Type

Business

Contact Information for Business Card

Paul Dunmore ( Owner) paul@dunmoreroofing-example.com, www.dunmoreroofing-example.com, Adress: 4172 Township road 43 Ashford Mills,ON K9X4T2

```html
<!DOCTYPE html>
<html lang="en">
<head>
<meta charset="utf-8">
<title>Dunmore Roofing – Business Card</title>
<link rel="stylesheet" href="https://fonts.googleapis.com/css2?family=Roboto:wght@400;500;900&family=Roboto+Condensed:wght@500&display=swap">
<style>
  :root {
    --backdrop: #2b2b2b;
    --card-dark: #171717;
    --brand-blue: #183f80;
    --name-blue: #1f4a93;
    --band-grey: #7b7b7b;
    --text-light: #c9c9c9;
    --text-muted: #8f8f8f;
    --white: #f4f4f4;
  }
  * { margin: 0; padding: 0; box-sizing: border-box; }
  html, body { width: 1200px; height: 960px; overflow: hidden; }
  body {
    position: relative;
    background: var(--backdrop);
    font-family: "Roboto", sans-serif;
  }
  .card {
    position: absolute;
    width: 600px;
    height: 343px;
    overflow: hidden;
  }
  .card-front { left: 314px; top: 113px; background: var(--card-dark); }
  .card-back  { left: 311px; top: 472px; background: var(--brand-blue); }

  .brand-name {
    position: absolute;
    font-family: "Roboto", sans-serif;
    font-weight: 900;
    text-transform: uppercase;
    line-height: 1.05;
  }
  .card-front .brand-name {
    left: 40px; top: 92px;
    font-size: 30px;
    letter-spacing: 1px;
    color: var(--name-blue);
  }
  .card-back .brand-name {
    left: 0; right: 0; top: 178px;
    text-align: center;
    font-size: 38px;
    letter-spacing: 1.5px;
    color: var(--white);
  }

  .contact {
    position: absolute;
    left: 39px; top: 200px;
    font-size: 14px;
    line-height: 19px;
    color: var(--text-light);
  }
  .contact .address { margin-bottom: 8px; }
  .contact-line { display: flex; align-items: center; gap: 8px; }
  .contact-line svg { width: 14px; height: 14px; fill: var(--text-light); }

  .person {
    position: absolute;
    right: 41px; top: 218px;
    text-align: right;
  }
  .person-name {
    font-family: "Roboto Condensed", sans-serif;
    font-weight: 500;
    font-size: 23px;
    color: var(--name-blue);
  }
  .person-title {
    font-size: 15px;
    color: var(--text-muted);
    margin-top: 2px;
  }

  .web-band {
    position: absolute;
    left: 0; bottom: 0;
    width: 600px; height: 28px;
  }
  .web-band-url {
    position: absolute;
    left: 40px; bottom: 6px;
    font-size: 14px;
    letter-spacing: 1px;
    color: var(--white);
  }

  .back-url {
    position: absolute;
    left: 0; right: 0; top: 285px;
    text-align: center;
    font-size: 15px;
    letter-spacing: 4.3px;
    color: var(--white);
  }
</style>
</head>
<body>
  <section class="card card-front">
    <div class="brand-name">Dunmore<br>Roofing</div>

    <div class="contact">
      <p class="address">4172 Township road 43<br>Ashford Mills, ON K9X4T2</p>
      <p class="contact-line">
        <svg viewBox="0 0 24 24" aria-hidden="true"><path d="M6.6 10.8a15.1 15.1 0 0 0 6.6 6.6l2.2-2.2c.3-.3.7-.4 1-.2 1.1.4 2.3.6 3.6.6.6 0 1 .4 1 1V20c0 .6-.4 1-1 1A17 17 0 0 1 3 4c0-.6.4-1 1-1h3.5c.6 0 1 .4 1 1 0 1.3.2 2.5.6 3.6.1.3 0 .7-.2 1z"/></svg>
        555 201 4870
      </p>
      <p class="contact-line">
        <svg viewBox="0 0 24 24" aria-hidden="true"><path d="M2 7.5 12 14l10-6.5V19H2z"/><path d="M2 5h20l-10 6.5z"/></svg>
        paul@dunmoreroofing-example.com
      </p>
    </div>

    <div class="person">
      <p class="person-name">PAUL DUNMORE</p>
      <p class="person-title">OWNER</p>
    </div>

    <svg class="web-band" viewBox="0 0 600 28" aria-hidden="true">
      <rect x="0" y="0" width="462" height="28" fill="var(--band-grey)"/>
      <rect x="462" y="0" width="138" height="28" fill="var(--brand-blue)"/>
      <polygon points="448,28 475,0 502,28" fill="var(--card-dark)"/>
      <polygon points="458,28 475,10 492,28" fill="var(--brand-blue)"/>
    </svg>
    <p class="web-band-url">www.dunmoreroofing-example.com</p>
  </section>

  <section class="card card-back">
    <div class="brand-name">Dunmore Roofing</div>
    <p class="back-url">www.dunmoreroofing-example.com</p>
  </section>
</body>
</html>
```